Brightmill Data Works

Our company is about IT hardwares and IT solutions. IT hardware such as PC, RAMS, storage and servers. IT solutions such as project management, BA. We are also selling new technology too.

Target Market(s)

Consumer, Small to Medium Business, Corporate

Requirements
Must have
• The business card must have the following:
• Name:
• Title:
• Contact Number:
• Email address:
• Website:
• Color: Must match the logo color upgrade

```html
<!DOCTYPE html>
<html lang="en">
<head>
<meta charset="utf-8">
<title>Brightmill Data Works – Business Card</title>
<link rel="stylesheet" href="https://fonts.googleapis.com/css2?family=Lato:wght@400;700;900&display=swap">
<style>
  :root {
    --page: #e9e6e1;
    --card-dark: #141414;
    --card-light: #f3f3f3;
    --ink-dark: #444444;
    --ink-white: #ffffff;
    --accent: #c4692a;
    --band-grey: #4a4a4a;
  }
  * { box-sizing: border-box; margin: 0; padding: 0; }
  html, body {
    width: 1200px; height: 900px; overflow: hidden;
    background: var(--page);
    font-family: "Lato", Arial, sans-serif;
  }
  .sheet {
    width: 1200px; height: 900px;
    display: flex; align-items: center; justify-content: center; gap: 40px;
  }
  .card {
    position: relative;
    width: 540px; height: 309px;
    overflow: hidden;
    box-shadow: 0 6px 18px rgba(0,0,0,.18);
  }

  /* Back side */
  .card-back {
    background: var(--card-dark);
    display: flex; flex-direction: column; align-items: center; justify-content: center;
    text-align: center;
  }
  .back-mark {
    width: 34px; height: 34px; background: var(--accent); margin-bottom: 20px;
  }
  .back-name {
    color: var(--ink-white);
    font-weight: 900; font-size: 30px; letter-spacing: 1px; text-transform: uppercase;
    line-height: 1.1;
  }
  .back-tagline {
    margin-top: 30px;
    color: var(--ink-white);
    font-size: 12px; letter-spacing: 3px; text-transform: uppercase;
  }

  /* Front side */
  .card-front { background: var(--card-light); }
  .front-wave { position: absolute; inset: 0; }
  .person { position: absolute; left: 40px; top: 66px; }
  .person-name {
    color: var(--accent); font-size: 19px; letter-spacing: .5px; text-transform: uppercase; font-weight: 400;
  }
  .person-title { color: var(--ink-dark); font-size: 15px; margin-top: 2px; }
  .front-brand {
    position: absolute; right: 36px; top: 70px; text-align: center;
  }
  .front-mark { width: 24px; height: 24px; background: var(--accent); margin: 0 auto 10px; }
  .front-name {
    color: var(--ink-dark); font-weight: 900; font-size: 22px; letter-spacing: .5px;
    text-transform: uppercase; line-height: 1.15;
  }
  .contacts {
    position: absolute; left: 40px; top: 180px; list-style: none;
  }
  .contacts li {
    display: flex; align-items: center; gap: 8px;
    color: var(--ink-dark); font-size: 14.5px; line-height: 20px;
  }
  .contacts svg { width: 12px; height: 12px; fill: var(--accent); flex: none; }
</style>
</head>
<body>
<main class="sheet">

  <section class="card card-back" aria-label="Business card back">
    <div class="back-mark"></div>
    <h1 class="back-name">Brightmill<br>Data Works</h1>
    <p class="back-tagline">IT Hardwares and IT Solutions</p>
  </section>

  <section class="card card-front" aria-label="Business card front">
    <svg class="front-wave" viewBox="0 0 540 309" preserveAspectRatio="none" aria-hidden="true">
      <path d="M0,272 C140,302 300,276 400,222 C450,196 500,188 540,186 L540,309 L0,309 Z" fill="var(--band-grey)"/>
      <path d="M0,250 C150,284 300,262 405,210 C305,272 150,294 0,264 Z" fill="var(--accent)"/>
    </svg>

    <div class="person">
      <h2 class="person-name">Daniel Hartley</h2>
      <p class="person-title">Managing Director</p>
    </div>

    <div class="front-brand">
      <div class="front-mark"></div>
      <p class="front-name">Brightmill<br>Data Works</p>
    </div>

    <ul class="contacts">
      <li>
        <svg viewBox="0 0 24 24"><path d="M6.6 10.8a15.1 15.1 0 0 0 6.6 6.6l2.2-2.2a1 1 0 0 1 1-.25 11.4 11.4 0 0 0 3.6.57 1 1 0 0 1 1 1V20a1 1 0 0 1-1 1A17 17 0 0 1 3 4a1 1 0 0 1 1-1h3.5a1 1 0 0 1 1 1c0 1.25.2 2.45.57 3.57a1 1 0 0 1-.25 1z"/></svg>
        044-555 010 234
      </li>
      <li>
        <svg viewBox="0 0 24 24"><path d="M2 5h20v14H2z M2 5l10 8 10-8" stroke="var(--card-light)" stroke-width="1.5"/></svg>
        info@brightmilldata.com
      </li>
      <li>
        <svg viewBox="0 0 24 24"><circle cx="12" cy="12" r="11"/><path d="M1 12h22M12 1c4 4 4 18 0 22M12 1c-4 4-4 18 0 22" stroke="var(--card-light)" stroke-width="1.5" fill="none"/></svg>
        www.brightmilldata.com
      </li>
    </ul>
  </section>

</main>
</body>
</html>
```